Business Card Design for Varomir Facility Services

We are looking for a Business Card Design for the Company "Varomir Facility Services."
Front side:
- Company Logo (small)
- Company Name, address, pohone, website and personal data.
- white background, for text e.g. company colors (blue or green like in the logo)
Please use following data:
Company data:
Varomir Facility Services Kostelac
Birkenhaldweg 14
6347 Rothalden
www.varomir-fs.ch
Person data:
Tarik Kostelac
Geschäftsführer
+41 76 519 47 83
info@varomir-fs.ch
Back side:
could be colored in blue or green
please use a big logo sing and some smaller icons to say what is all beeing offered in facility services, like cleaning, maintenance cleaning
industrial cleaning, caretaking, gardening, disposal. There is no need for everyone of the icons if there are similar or an icon is standing for more of them.
colors to use:
blue: HEX 246BB0
green: HEX 52B33E

```html
<!DOCTYPE html>
<html lang="de">
<head>
<meta charset="utf-8">
<title>Varomir Facility Services – Business Card</title>
<link href="https://fonts.googleapis.com/css2?family=Source+Sans+3:wght@400;600&display=swap" rel="stylesheet">
<style>
  :root{
    --brand-blue:#1668b2;
    --brand-green:#52b33e;
    --paper:#ffffff;
    --stage:#ffffff;
    --ink-light:#ffffff;
  }
  *{margin:0;padding:0;box-sizing:border-box}
  html,body{width:1200px;height:960px;overflow:hidden;background:var(--stage)}
  body{position:relative;font-family:"Source Sans 3",sans-serif}
  .card{
    position:absolute;left:286px;width:629px;height:360px;
    background:var(--paper);overflow:hidden;
    box-shadow:0 2px 4px rgba(0,0,0,.25),0 0 2px rgba(0,0,0,.12);
  }
  .card--front{top:109px}
  .card--back{top:492px}
  .card__tab{
    position:absolute;left:0;top:67px;width:22px;height:224px;
    background:var(--brand-blue);border-radius:0 7px 7px 0;
  }
  .card__panel{
    position:absolute;left:336px;top:0;right:0;bottom:0;
    background:var(--brand-blue);color:var(--ink-light);
  }
  .brand{
    position:absolute;left:40px;top:0;width:270px;height:360px;
    display:flex;align-items:center;justify-content:center;gap:10px;
  }
  .brand__dot{width:14px;height:14px;border-radius:50%;background:var(--brand-green);flex:none}
  .brand__name{
    color:var(--brand-blue);font-weight:600;font-size:25px;line-height:1.1;
  }
  .contact{position:absolute;left:44px;top:0;right:10px}
  .contact__name{position:absolute;top:72px;font-size:24px;font-weight:600;white-space:nowrap}
  .contact__role{position:absolute;top:102px;font-size:20px;font-weight:400;white-space:nowrap}
  .contact__address{position:absolute;top:149px;font-size:17.5px;line-height:26.5px;white-space:nowrap}
  .contact__line{
    position:absolute;left:0;font-size:17.5px;height:20px;
    display:flex;align-items:center;white-space:nowrap;
  }
  .contact__line svg{width:16px;height:16px;margin-right:15px;flex:none}
  .contact__line--phone{top:211px}
  .contact__line--mail{top:237px}
  .contact__line--web{top:264px}
  .services{position:absolute;left:44px;top:101px;list-style:none}
  .services li{
    display:flex;align-items:center;height:26.3px;font-size:17.5px;white-space:nowrap;
  }
  .services svg{width:16px;height:16px;margin-right:14px;flex:none}
</style>
</head>
<body>

<section class="card card--front">
  <div class="card__tab"></div>
  <div class="brand">
    <span class="brand__dot"></span>
    <span class="brand__name">Varomir<br>Facility Services</span>
  </div>
  <div class="card__panel">
    <div class="contact">
      <p class="contact__name">Tarik Kostelac</p>
      <p class="contact__role">Geschäftsführer</p>
      <p class="contact__address">Birkenhaldweg 14<br>6347 Rothalden</p>
      <p class="contact__line contact__line--phone">
        <svg viewBox="0 0 16 16" aria-hidden="true"><path fill="#fff" d="M3 1l3 3-1.5 2c1 2 2.5 3.5 4.5 4.5L11 9l3 3-2 2.5C6.5 14 2 9.5 1 3z"/></svg>
        +41 76 519 47 83
      </p>
      <p class="contact__line contact__line--mail">
        <svg viewBox="0 0 16 16" aria-hidden="true"><rect x="1" y="3.5" width="14" height="10" fill="#fff"/><path d="M1.5 4l6.5 5 6.5-5M1.5 13l5-4.5M14.5 13l-5-4.5" stroke="#1668b2" stroke-width="1.2" fill="none"/></svg>
        info@varomir-fs.ch
      </p>
      <p class="contact__line contact__line--web">
        <svg viewBox="0 0 16 16" aria-hidden="true"><circle cx="8" cy="8" r="7" fill="#fff"/><path d="M1 8h14M8 1c-3 3-3 11 0 14M8 1c3 3 3 11 0 14" stroke="#1668b2" stroke-width="1.2" fill="none"/></svg>
        www.varomir-fs.ch
      </p>
    </div>
  </div>
</section>

<section class="card card--back">
  <div class="card__tab"></div>
  <div class="brand">
    <span class="brand__dot"></span>
    <span class="brand__name">Varomir<br>Facility Services</span>
  </div>
  <div class="card__panel">
    <ul class="services">
      <li><svg viewBox="0 0 16 16" aria-hidden="true"><path fill="#fff" d="M8 0l1.6 6.4L16 8l-6.4 1.6L8 16 6.4 9.6 0 8l6.4-1.6z"/></svg>Like cleaning</li>
      <li><svg viewBox="0 0 16 16" aria-hidden="true"><path fill="#fff" d="M8 0l1.6 6.4L16 8l-6.4 1.6L8 16 6.4 9.6 0 8l6.4-1.6z"/></svg>Maintenance cleaning</li>
      <li><svg viewBox="0 0 16 16" aria-hidden="true"><path fill="#fff" d="M8 0l1.6 6.4L16 8l-6.4 1.6L8 16 6.4 9.6 0 8l6.4-1.6z"/></svg>Industrial cleaning</li>
      <li><svg viewBox="0 0 16 16" aria-hidden="true"><path fill="#fff" d="M8 0l1.6 6.4L16 8l-6.4 1.6L8 16 6.4 9.6 0 8l6.4-1.6z"/></svg>Caretaking</li>
      <li><svg viewBox="0 0 16 16" aria-hidden="true"><path fill="#fff" d="M8 0l1.6 6.4L16 8l-6.4 1.6L8 16 6.4 9.6 0 8l6.4-1.6z"/></svg>Gardening</li>
      <li><svg viewBox="0 0 16 16" aria-hidden="true"><path fill="#fff" d="M8 0l1.6 6.4L16 8l-6.4 1.6L8 16 6.4 9.6 0 8l6.4-1.6z"/></svg>Disposal</li>
    </ul>
  </div>
</section>

</body>
</html>
```